Website for an electrical contractor :)

We are after a web site which can show pictures of our jobs and our capability in a professional, creative and easily understood way.

----- Brightvale Electrical ------

We really want a visually good looking website with three sections

Section one:
'Completed projects'
We have a few pictures of jobs which we've completed and would like to show off with a brief description. (see uploads)

Section two:
'Our capabilities'
Just a list of what services we offer

Section three:
We would like a 'contact us' section which people can send us a short msg and upload a file for plans to be able to send to us. We would need their name, phone number and email details. We would also need a short privacy policy saying 'we do not disclose information to third parties'.
We also want to display our contact number and postal address

Good luck :)

Target Market(s)

Adults 25 years+
Business owners
Builders
Real estate agents

Industry/Entity Type

Electrical

Colors

Designer to choose colors to be used in the design.

Requirements
Must have
• Visually appealing
Easy to understand
In the 'Completed projects' section, must have a list for each project we do i can upload pictures for it.

```html
<!DOCTYPE html>
<html lang="en">
<head>
<meta charset="utf-8">
<title>Brightvale Electrical</title>
<link href="https://fonts.googleapis.com/css2?family=Raleway:wght@400;500;600&family=Open+Sans:wght@400;600;700&family=Ubuntu:wght@500&display=swap" rel="stylesheet">
<style>
:root{
  --red:#e31e24;
  --dark:#1f1f1f;
  --band:#2c2c2c;
  --ink:#333;
  --muted:#777;
  --light:#f2f2f2;
  --grey:#dedede;
  --white:#fff;
  --foot:#121212;
}
*{margin:0;padding:0;box-sizing:border-box}
html,body{width:744px;height:1200px;overflow:hidden}
body{position:relative;font-family:'Open Sans',sans-serif;color:var(--ink);background:var(--white)}
.abs{position:absolute}
.hero{left:0;top:0;width:744px;height:256px;background:linear-gradient(180deg,#b9bfc6 0%,#9ea3a7 45%,#8a8886 70%,#b7b1a9 100%)}
.header{left:93px;top:0;width:558px;height:46px;background:var(--white)}
.logo{left:10px;top:10px;display:flex;align-items:center;gap:6px}
.logo .dot{width:14px;height:14px;border-radius:50%;background:var(--red)}
.logo .name{font-family:'Raleway',sans-serif;font-size:24px;color:#555;letter-spacing:-.5px}
.contact-top{right:10px;top:16px;display:flex;align-items:center;gap:8px;font-size:9.5px;color:#666}
.contact-top svg{width:10px;height:10px}
.soc{width:13px;height:13px;background:#333}
.soc.blue{background:#1d5fb4}
.nav{left:93px;top:46px;width:558px;height:23px;background:var(--dark);display:flex;align-items:center;padding-left:10px}
.nav a{font-size:7px;color:#ddd;text-decoration:none;margin-right:34px}
.nav a.active{background:#333;color:var(--white);font-weight:700;padding:5px 10px;margin-right:26px}
.search{right:8px;top:5px;width:126px;height:13px;display:flex}
.search span{flex:1;background:var(--white);font-size:5.5px;color:#999;padding:3px 8px}
.search i{width:13px;background:#222}
.cap{font-family:'Ubuntu',sans-serif;font-size:18px;color:var(--white);text-align:center}
.cap1{left:282px;top:134px;width:180px;height:28px;background:var(--red);line-height:28px}
.cap2{left:310px;top:163px;width:124px;height:27px;background:var(--dark);line-height:27px}
.dots{left:358px;top:243px;display:flex;gap:3px}
.dots b{width:8px;height:8px;border-radius:50%;background:var(--red)}
.dots b.on{background:var(--dark)}
.welcome{left:0;top:256px;width:744px;height:93px;background:var(--band);text-align:center}
.welcome h1{font-family:'Raleway',sans-serif;font-weight:400;font-size:15px;color:var(--white);margin-top:18px;display:flex;justify-content:center;align-items:baseline;gap:4px}
.welcome h1 .dot{width:9px;height:9px;border-radius:50%;background:var(--red);align-self:center;margin-right:4px}
.welcome h1 strong{color:var(--red);font-weight:600;font-size:17px}
.welcome h1 small{font-size:9px}
.welcome p{font-size:6.5px;line-height:9.5px;color:#999;width:360px;margin:10px auto 0}
.sec-title{font-family:'Raleway',sans-serif;font-weight:600;font-size:14px;color:var(--red);text-align:center;width:744px;left:0}
.sec-text{left:192px;width:360px;font-size:5.3px;line-height:7px;color:#666;text-align:center}
.card{top:427px;width:172px;height:140px;background:var(--white);border:1px solid #ddd;display:flex;box-shadow:0 6px 6px -4px rgba(0,0,0,.25)}
.card.feat{background:var(--dark);border-color:var(--red)}
.card .ph{width:92px;height:100%}
.card .txt{padding:21px 8px 0 9px;flex:1}
.card h3{font-family:'Raleway',sans-serif;font-weight:500;font-size:8.5px;color:var(--red);line-height:10px}
.card h3 small{display:block;font-size:6.5px;color:#555;font-weight:400}
.card.feat h3 small{color:var(--red)}
.card p{font-size:5.3px;line-height:8px;color:#888;margin-top:13px}
.card.feat p{color:#ddd}
.btn{display:inline-block;font-size:5.5px;font-weight:700;color:var(--white);background:var(--dark);padding:6px 9px;margin-top:13px}
.btn.red{background:var(--red)}
.caps-bg{left:0;top:590px;width:744px;height:364px;background:var(--light)}
.frame{top:666px;width:266px;height:166px;background:var(--white);border:1px solid #ddd;padding:5px}
.frame div{width:100%;height:100%}
.cap-h{font-family:'Raleway',sans-serif;font-weight:500;font-size:11.5px;color:#222;top:845px}
.list{top:866px;width:270px;display:grid;grid-template-columns:140px 130px;row-gap:5px;font-size:5.4px;font-weight:600;color:#444;list-style:none}
.list li{display:flex;align-items:center;gap:6px;height:9px}
.list li::before{content:"";width:3px;height:3px;background:#333}
.list li.hl{background:var(--red);color:var(--white);padding-left:5px;width:125px}
.list li.hl::before{background:var(--white)}
.rm{top:910px;font-size:5.5px;font-weight:600;color:var(--white);background:var(--red);padding:6px 13px;border:1px solid #b8151a}
.contact{left:0;top:954px;width:744px;height:106px;background:var(--grey)}
.contact h2{font-family:'Raleway',sans-serif;font-weight:600;font-size:12.5px;color:var(--red);position:absolute;left:99px;top:11px}
.field{background:var(--light);border:1px solid #e8e8e8;font-size:5px;color:#999;padding:4px 5px;height:14px}
.upload{left:518px;top:984px;width:126px;height:14px;background:var(--dark);border:1px solid var(--red);color:var(--white);font-size:6.5px;font-weight:600;text-align:center;line-height:12px}
.submit{left:518px;top:1006px;width:126px;height:33px;background:var(--red);color:var(--white);font-size:8px;font-weight:700;text-align:center;line-height:33px;border:1px solid #b8151a}
.footer{left:0;top:1060px;width:744px;height:116px;background:var(--foot)}
.f-h{font-family:'Raleway',sans-serif;font-weight:500;font-size:9.5px;color:var(--red);top:1082px}
.f-logo{left:100px;top:1083px;display:flex;align-items:center;gap:4px}
.f-logo .dot{width:9px;height:9px;border-radius:50%;background:var(--red)}
.f-logo .name{font-family:'Raleway',sans-serif;font-size:15px;color:#888}
.f-text{left:100px;top:1116px;width:124px;font-size:5.2px;line-height:8px;color:#777}
.f-soc{left:240px;top:1105px;display:flex;gap:6px}
.f-soc b{width:13px;height:13px;border-radius:50%;background:#333}
.f-soc b.on{background:#1d5fb4}
.f-row{font-size:6px;color:#888;display:flex;gap:7px;line-height:9px}
.f-row svg{width:7px;height:7px;flex:none;margin-top:1px}
.copy{left:0;top:1176px;width:744px;height:24px;background:var(--foot);border-top:1px solid #7a1013;text-align:center;font-size:5px;color:var(--red);line-height:22px}
</style>
</head>
<body>

<div class="abs hero" role="img" aria-label="Photo of a concrete commercial building under construction with an electrician's van"></div>

<header class="abs header">
  <div class="abs logo"><span class="dot"></span><span class="name">Brightvale</span></div>
  <div class="abs contact-top">
    <svg viewBox="0 0 10 10"><rect x="0.5" y="2" width="9" height="6" fill="none" stroke="#888"/><path d="M0.5 2 5 6 9.5 2" fill="none" stroke="#888"/></svg>
    <span style="font-size:10px">info@brightvaleelectrical.com.au</span>
    <svg viewBox="0 0 10 10" style="margin-left:6px"><path d="M2 1h2l1 2.5-1.3 1a6 6 0 0 0 2.8 2.8l1-1.3L10 7v2h-1A8 8 0 0 1 1 2V1z" fill="#888"/></svg>
    <span style="font-size:10px">04 5550 1827</span>
    <span class="soc blue" style="margin-left:8px"></span><span class="soc"></span><span class="soc"></span>
  </div>
</header>

<nav class="abs nav">
  <a class="active">Home</a><a>About Us</a><a>Our Projects</a><a>Our Capabilities</a><a>Blog</a><a>Contact Us</a>
  <div class="abs search"><span>Search here</span><i></i></div>
</nav>

<div class="abs cap cap1">Development and</div>
<div class="abs cap cap2">Installation</div>
<div class="abs dots"><b></b><b class="on"></b><b></b></div>

<section class="abs welcome">
  <h1><span class="dot"></span>Welcome To <strong>Brightvale</strong><small>Electrical &amp; Communications</small></h1>
  <p>Lorem Ipsum is simply dummy text of the printing and typesetting industry. Lorem Ipsum has been the industry's standard dummy text ever since the 1500s, when an unknown printer took a galley of type and scrambled it to make a type specimen book.</p>
</section>

<h2 class="abs sec-title" style="top:373px">Our Projects</h2>
<p class="abs sec-text" style="top:399px">Lorem Ipsum is simply dummy text of the printing and typesetting industry. Lorem Ipsum has been the industry's standard dummy text ever since the 1500s, when an unknown printer took a galley of type and scrambled it to make a type specimen book.</p>

<article class="abs card feat" style="left:100px">
  <div class="ph" role="img" aria-label="Photo of a finished office lounge with white armchairs" style="background:linear-gradient(180deg,#cfcbc6,#a9a39c)"></div>
  <div class="txt"><h3>Lorem Ipsum<small>is simply dummy</small></h3><p>Lorem Ipsum is simply dummy text of the printing.</p><span class="btn red">Read More</span></div>
</article>
<article class="abs card" style="left:286px">
  <div class="ph" role="img" aria-label="Photo of conduit cabling laid on a building slab" style="background:linear-gradient(180deg,#a9b4bd,#6f6b66)"></div>
  <div class="txt"><h3>Lorem Ipsum<small>is simply dummy</small></h3><p>Lorem Ipsum is simply dummy text of the printing.</p><span class="btn">Read More</span></div>
</article>
<article class="abs card" style="left:473px">
  <div class="ph" role="img" aria-label="Photo of a fitted-out kitchen with downlights" style="background:linear-gradient(180deg,#d8d3cb,#8c8680)"></div>
  <div class="txt"><h3>Lorem Ipsum<small>is simply dummy</small></h3><p>Lorem Ipsum is simply dummy text of the printing.</p><span class="btn">Read More</span></div>
</article>

<div class="abs caps-bg"></div>
<h2 class="abs sec-title" style="top:610px">Our Capabilities</h2>
<p class="abs sec-text" style="top:637px">Lorem Ipsum is simply dummy text of the printing and typesetting industry. Lorem Ipsum has been the industry's standard dummy text ever since the 1500s, when an unknown printer took a galley of type and scrambled it to make a type specimen book.</p>

<div class="abs frame" style="left:99px"><div role="img" aria-label="Photo of new residential townhouses with a paved driveway" style="background:linear-gradient(180deg,#5b9fd9 0%,#8fc0e6 35%,#6d6a63 60%,#4a4a4a 100%)"></div></div>
<div class="abs frame" style="left:378px"><div role="img" aria-label="Photo of a concrete commercial warehouse building" style="background:linear-gradient(180deg,#2a6fc4 0%,#6aa3dd 30%,#c9c7c2 55%,#a6a29b 100%)"></div></div>

<h3 class="abs cap-h" style="left:99px">Residential Capability Statement</h3>
<ul class="abs list" style="left:100px">
  <li class="hl">24hr Support / faults</li><li>Ceiling fans</li>
  <li>Mains/sub mains cabling</li><li>Exhaust fans</li>
  <li>RCD (Safety Switch) installations</li><li>Kitchen / Bathroom Projects</li>
</ul>
<span class="abs rm" style="left:101px">Read More</span>

<h3 class="abs cap-h" style="left:378px">Commercial / Industrial Capability Statement</h3>
<ul class="abs list" style="left:379px">
  <li>24hr Support / faults</li><li>Phone/data points</li>
  <li>Lighting/power design and consultation</li><li>Data cabinets</li>
  <li>Emergency and exit lighting</li><li>Data Networking</li>
</ul>
<span class="abs rm" style="left:379px">Read More</span>

<section class="abs contact"><h2>Contact From</h2></section>
<div class="abs field" style="left:99px;top:984px;width:127px">Enter Your Name :</div>
<div class="abs field" style="left:239px;top:984px;width:127px">Enter Your Email :</div>
<div class="abs field" style="left:378px;top:984px;width:127px">Enter Your Phone :</div>
<div class="abs upload">Upload File</div>
<div class="abs field" style="left:99px;top:1006px;width:405px;height:33px">Massage :</div>
<div class="abs submit">SUBMIT</div>

<footer class="abs footer"></footer>
<div class="abs f-logo"><span class="dot"></span><span class="name">Brightvale</span></div>
<p class="abs f-text">Lorem Ipsum is simply dummy text of the printing and typesetting industry. Lorem Ipsum has been the industry's standard dummy text ever since</p>

<h4 class="abs f-h" style="left:239px">Follow Us On</h4>
<div class="abs f-soc"><b class="on"></b><b></b><b></b></div>

<h4 class="abs f-h" style="left:378px">Location</h4>
<div class="abs f-row" style="left:378px;top:1103px">
  <svg viewBox="0 0 10 10"><path d="M5 0a3.5 3.5 0 0 0-3.5 3.5C1.5 6 5 10 5 10s3.5-4 3.5-6.5A3.5 3.5 0 0 0 5 0z" fill="#666"/><circle cx="5" cy="3.5" r="1.2" fill="#121212"/></svg>
  <span>P.O Box 417 Harbour Point W.A<br>6000 A.B.N: 12 345 678 901</span>
</div>

<h4 class="abs f-h" style="left:518px">Contact Info</h4>
<div class="abs f-row" style="left:518px;top:1100px">
  <svg viewBox="0 0 10 10"><path d="M2 1h2l1 2.5-1.3 1a6 6 0 0 0 2.8 2.8l1-1.3L10 7v2h-1A8 8 0 0 1 1 2V1z" fill="#666"/></svg><span>04 5550 1827</span>
</div>
<div class="abs f-row" style="left:518px;top:1115px">
  <svg viewBox="0 0 10 10"><rect x="2" y="1" width="6" height="3" fill="#666"/><rect x="0.5" y="4" width="9" height="4" fill="#666"/><rect x="2.5" y="6.5" width="5" height="3" fill="#999"/></svg><span>08 5550 3946</span>
</div>
<div class="abs f-row" style="left:518px;top:1129px">
  <svg viewBox="0 0 10 10"><rect x="0.5" y="2" width="9" height="6" fill="#666"/><path d="M0.5 2 5 6 9.5 2" fill="none" stroke="#121212"/></svg><span>info@brightvaleelectrical.com.au</span>
</div>

<div class="abs copy">All Copyrights Reserved © Brightvale Electrical 2015. Privacy Policy</div>

</body>
</html>
```